Business Card Design

Business Card for professional consulting firm working with large financial institutions.

Target Market(s)

Executive buyers

Industry/Entity Type

Banking

Contact Information for Business Card

Mild creativity wanted. Not boring, but do elaborate artwork.

Font styles to use
Serif
Sans Serif

Colors

Designer to choose colors to be used in the design.

Requirements
Must have
• Standard business card features - company name, individual name, telephone, website, email, locations.
Nice to have
• Two colors
Should not have
• too many colors, fancy printing, cartoons.

```html
<!DOCTYPE html>
<html lang="en">
<head>
<meta charset="utf-8">
<title>Harborline Consulting — Business Card</title>
<link rel="stylesheet" href="https://fonts.googleapis.com/css2?family=Roboto+Slab:wght@300;400&family=Roboto:wght@300;400&display=swap">
<style>
  :root {
    --backdrop: #d8d3cc;
    --card-light: #eeeeef;
    --card-mid: #d3d4d7;
    --card-dark: #0b0b0c;
    --card-dark-edge: #1e1e20;
    --ink: #2a2a2c;
    --name: #e6d3d0;
    --title: #d2a5a5;
    --detail: #bdb29f;
    --divider: #6e5d4f;
  }
  * { margin: 0; padding: 0; box-sizing: border-box; }
  html, body { width: 1200px; height: 969px; overflow: hidden; }
  body { background: var(--backdrop); position: relative; }

  .card {
    position: absolute;
    left: 120px; top: 205px;
    width: 960px; height: 560px;
    border-radius: 22px;
    overflow: hidden;
    box-shadow: 0 14px 40px rgba(0,0,0,0.25);
  }
  .card-shapes { position: absolute; inset: 0; }

  .brand {
    position: absolute;
    left: 0; width: 920px; top: 112px;
    text-align: center;
    font-family: "Roboto", sans-serif;
    font-weight: 300;
    font-size: 40px;
    letter-spacing: 6px;
    text-transform: uppercase;
    color: var(--ink);
    white-space: nowrap;
  }

  .person {
    position: absolute;
    right: 523px;
    top: 388px;
    text-align: right;
  }
  .person-name {
    font-family: "Roboto Slab", serif;
    font-weight: 300;
    font-size: 34px;
    letter-spacing: 1px;
    color: var(--name);
    line-height: 1.1;
    white-space: nowrap;
  }
  .person-title {
    font-family: "Roboto", sans-serif;
    font-weight: 400;
    font-size: 22px;
    letter-spacing: 0.5px;
    color: var(--title);
    margin-top: 2px;
  }

  .divider {
    position: absolute;
    left: 482px; top: 360px;
    width: 1px; height: 145px;
    background: var(--divider);
  }

  .contact {
    position: absolute;
    left: 523px; top: 362px;
    font-family: "Roboto", sans-serif;
    font-weight: 300;
    font-size: 22px;
    color: var(--detail);
    line-height: 29px;
    white-space: nowrap;
  }
  .contact-address { margin-bottom: 17px; }
  .contact-row { display: flex; align-items: center; gap: 14px; height: 32px; }
  .contact-row svg { width: 20px; height: 20px; flex: none; fill: var(--detail); }
</style>
</head>
<body>
  <div class="card">
    <svg class="card-shapes" viewBox="0 0 960 560" width="960" height="560" aria-hidden="true">
      <defs>
        <linearGradient id="frost" x1="0" y1="0" x2="0" y2="1">
          <stop offset="0" stop-color="#eeeeef"/>
          <stop offset="1" stop-color="#d3d4d7"/>
        </linearGradient>
        <linearGradient id="silver-band" x1="0" y1="0" x2="1" y2="0">
          <stop offset="0" stop-color="#8e9196"/>
          <stop offset="0.5" stop-color="#e4e6e9"/>
          <stop offset="1" stop-color="#9a9da2"/>
        </linearGradient>
        <linearGradient id="dark-panel" x1="0" y1="0" x2="0" y2="1">
          <stop offset="0" stop-color="#1e1e20"/>
          <stop offset="0.3" stop-color="#0b0b0c"/>
          <stop offset="1" stop-color="#0b0b0c"/>
        </linearGradient>
      </defs>
      <rect width="960" height="560" fill="url(#frost)"/>
      <path d="M0 236 C 260 300, 640 300, 960 222 L 960 250 C 640 318, 260 318, 0 258 Z" fill="url(#silver-band)" opacity="0.9"/>
      <path d="M0 264 C 260 322, 640 322, 960 256 L 960 560 L 0 560 Z" fill="url(#dark-panel)"/>
    </svg>

    <div class="brand">Harborline Consulting</div>

    <div class="person">
      <div class="person-name">PAUL REYES</div>
      <div class="person-title">CEO/FOUNDER</div>
    </div>

    <div class="divider"></div>

    <div class="contact">
      <div class="contact-address">4120 Willow Court<br>Fairbanks, Alaska 99701</div>
      <div class="contact-row">
        <svg viewBox="0 0 24 24" aria-hidden="true"><path d="M6.6 10.8a15.1 15.1 0 0 0 6.6 6.6l2.2-2.2a1 1 0 0 1 1-.25 11.4 11.4 0 0 0 3.6.57 1 1 0 0 1 1 1V20a1 1 0 0 1-1 1A17 17 0 0 1 3 4a1 1 0 0 1 1-1h3.5a1 1 0 0 1 1 1c0 1.25.2 2.45.57 3.57a1 1 0 0 1-.25 1z"/></svg>
        <span>555 214 7390</span>
      </div>
      <div class="contact-row">
        <svg viewBox="0 0 24 24" aria-hidden="true"><path d="M2 5h20v2l-10 6.5L2 7z"/><path d="M2 9l10 6.5L22 9v10H2z"/></svg>
        <span>info@harborlinecg.com</span>
      </div>
    </div>
  </div>
</body>
</html>
```